Civora88 - a Political Plebescite app.

There is a current app in the App Store (worldwide) and Play Store (worldwide) called yourStance (with an owl logo). The UX needs to be redesigned to make it more visually pleasing.

The requirement is to build a UX that is suitable for both iOS and Android - i.e. consistent look for both platforms. The design is to span the variety of sizes available from smart devices - phones and tablets. The layout as it stands is portrait only, and a secondary design to encompass landscape is wanted.

You would need to download the app to get a feel for all the functionality - there are 3 visible forms (currently) and a hidden form, that will be used in the near future - this hidden form will look similar to the main (first) form.

To get full functionality you need to do the following:
Go to the Options page
Toggle the top slide
Click on UNREGISTERED
Select a state/territory

I know this is a bit non-intuitive - in the "real" product these steps are automated - but for this release the user gets to choose.

Once this is done - the other button(s) appear in the top left of the screen - and data is available to be displayed.

The current forms are included in this brief. The Options screen will ultimately not be showing all the current data, only the lower slider (or other indicator) and the associated version and copyright notices. The hidden screen is much like the main screen - showing the name of the bill and information pertaining to that bill - there needs to be a button (or action site) to toggle between the main and this hidden screen.

Target Market(s)

All eligable voters (currently in Australia)

Industry/Entity Type

Political

Requirements
Should not have
• Do not present to me my own/existing design with the only change being colours and label layout.

```html
<!DOCTYPE html>
<html lang="en">
<head>
<meta charset="utf-8">
<title>Civora88 – Bill</title>
<link rel="stylesheet" href="https://fonts.googleapis.com/css2?family=Lato:wght@400;700&display=swap">
<style>
  :root {
    --black: #000000;
    --white: #ffffff;
    --band: #e9e9e9;
    --ink: #3a3a3a;
    --ink-soft: #444444;
    --blue: #1b8fe6;
    --red: #f52a1c;
    --red-label: #e8261a;
    --navy: #1f2d45;
    --green: #0a9a2a;
    --green-label: #0a8a25;
    --map-green: #2e8a68;
    --map-red: #b23a2a;
    --glow: #2fb6ff;
    --dot: #0fa82a;
  }
  * { box-sizing: border-box; margin: 0; padding: 0; }
  html, body { width: 675px; height: 1200px; overflow: hidden; background: var(--white); }
  body { font-family: "Lato", sans-serif; position: relative; }

  .status-bar {
    position: absolute; left: 0; top: 0; width: 675px; height: 40px;
    background: var(--black); color: var(--white); font-size: 22px;
    display: flex; align-items: center; padding: 0 10px;
  }
  .status-bar .carrier { display: flex; align-items: center; gap: 6px; }
  .status-bar .time { position: absolute; left: 0; right: 0; text-align: center; top: 8px; }
  .status-bar .right { margin-left: auto; display: flex; align-items: center; gap: 10px; }

  .nav-bar {
    position: absolute; left: 0; top: 40px; width: 675px; height: 86px;
    background: var(--black); color: var(--white);
  }
  .region-switch { position: absolute; left: 18px; top: 24px; display: flex; gap: 8px; }
  .region {
    width: 42px; height: 34px; border-radius: 6px;
  }
  .region.green { background: var(--map-green); }
  .region.red { background: var(--map-red); }
  .region.active { box-shadow: 0 0 10px 3px var(--glow); }
  .nav-title {
    position: absolute; left: 0; right: 0; top: 26px; text-align: center;
    font-size: 27px; font-weight: 700;
  }
  .help-button { position: absolute; left: 568px; top: 24px; }
  .settings-button { position: absolute; left: 621px; top: 24px; }

  .bill-header {
    position: absolute; left: 0; top: 126px; width: 675px; height: 59px;
    background: var(--band); display: flex; align-items: center; padding: 0 18px;
  }
  .bill-title { font-size: 28px; font-weight: 400; color: var(--ink); }
  .bill-status { position: absolute; right: 14px; top: 10px; }

  .bill-summary {
    position: absolute; left: 18px; top: 204px; width: 640px;
    font-size: 18.6px; line-height: 25.6px; color: var(--ink-soft);
    hyphens: auto; -webkit-hyphens: auto;
  }

  .vote-actions {
    position: absolute; left: 0; top: 1007px; width: 675px;
    display: flex; justify-content: center; gap: 31px;
  }
  .vote { display: flex; flex-direction: column; align-items: center; width: 66px; }
  .vote-circle {
    width: 66px; height: 66px; border-radius: 50%;
    display: flex; align-items: center; justify-content: center;
  }
  .vote-label { margin-top: 14px; font-size: 19px; }
  .vote.no .vote-circle { background: var(--red); }
  .vote.no .vote-label { color: var(--red-label); }
  .vote.party .vote-circle { background: var(--navy); }
  .vote.party .vote-label { color: var(--navy); }
  .vote.yes .vote-circle { background: var(--green); }
  .vote.yes .vote-label { color: var(--green-label); }

  .chamber-bar {
    position: absolute; left: 0; top: 1160px; width: 675px; height: 40px;
    background: var(--black); color: var(--white); font-size: 18px;
    display: flex; align-items: center;
  }
  .chamber-bar .live-dot {
    position: absolute; left: 19px; width: 16px; height: 16px; border-radius: 50%; background: var(--dot);
  }
  .chamber-bar .chamber { position: absolute; left: 0; right: 0; text-align: center; }
  .chamber-bar .count { position: absolute; right: 18px; }
</style>
</head>
<body>
  <header class="status-bar">
    <div class="carrier">
      <svg width="80" height="14" viewBox="0 0 80 14" aria-hidden="true">
        <circle cx="7" cy="7" r="6" fill="#fff"/>
        <circle cx="22" cy="7" r="6" fill="#fff"/>
        <circle cx="37" cy="7" r="5.3" fill="none" stroke="#fff" stroke-width="1.4"/>
        <circle cx="52" cy="7" r="5.3" fill="none" stroke="#fff" stroke-width="1.4"/>
        <circle cx="67" cy="7" r="5.3" fill="none" stroke="#fff" stroke-width="1.4"/>
      </svg>
      <span>KOALA</span>
      <svg width="24" height="18" viewBox="0 0 24 18" aria-hidden="true">
        <path d="M2 6 A14 14 0 0 1 22 6" fill="none" stroke="#fff" stroke-width="2.5"/>
        <path d="M6 10 A8 8 0 0 1 18 10" fill="none" stroke="#fff" stroke-width="2.5"/>
        <circle cx="12" cy="15" r="2.5" fill="#fff"/>
      </svg>
    </div>
    <span class="time">4:21 PM</span>
    <div class="right">
      <svg width="12" height="22" viewBox="0 0 12 22" aria-hidden="true">
        <path d="M1 6 L11 15 L6 20 L6 2 L11 7 L1 16" fill="none" stroke="#999" stroke-width="1.6"/>
      </svg>
      <span>100%</span>
      <svg width="38" height="18" viewBox="0 0 38 18" aria-hidden="true">
        <rect x="1" y="1" width="32" height="16" rx="3" fill="none" stroke="#fff" stroke-width="1.6"/>
        <rect x="3.5" y="3.5" width="27" height="11" rx="1.5" fill="#fff"/>
        <rect x="34" y="6" width="3" height="6" rx="1" fill="#fff"/>
      </svg>
    </div>
  </header>

  <nav class="nav-bar">
    <div class="region-switch">
      <div class="region green" role="img" aria-label="Map of Australia, federal view"></div>
      <div class="region red active" role="img" aria-label="Map of Australia, selected state"></div>
      <div class="region green" role="img" aria-label="Map of Australia, house view"></div>
      <div class="region red" role="img" aria-label="Map of Australia, senate view"></div>
    </div>
    <h1 class="nav-title">Title</h1>
    <svg class="help-button" width="36" height="36" viewBox="0 0 36 36" aria-label="Help">
      <circle cx="18" cy="18" r="17" fill="var(--blue)"/>
      <text x="18" y="25" text-anchor="middle" font-family="Lato, sans-serif" font-weight="700" font-size="20" fill="#000">?</text>
    </svg>
    <svg class="settings-button" width="36" height="36" viewBox="0 0 36 36" aria-label="Settings">
      <circle cx="18" cy="18" r="13" fill="none" stroke="var(--blue)" stroke-width="7" stroke-dasharray="5.1 5.1"/>
      <circle cx="18" cy="18" r="10" fill="var(--blue)"/>
      <circle cx="18" cy="18" r="4.5" fill="var(--black)"/>
    </svg>
  </nav>

  <section class="bill-header">
    <h2 class="bill-title">Crimes Amendment (Ava's Law) Bill 2015</h2>
    <svg class="bill-status" width="40" height="40" viewBox="0 0 40 40" aria-label="Bill not passed">
      <rect x="12" y="9" width="16" height="21" fill="#fff" stroke="#333" stroke-width="1.6"/>
      <path d="M15 14h10M15 18h10M15 22h10M15 26h7" stroke="#333" stroke-width="1.4"/>
      <circle cx="20" cy="20" r="17.5" fill="none" stroke="var(--red)" stroke-width="2.5"/>
      <path d="M8 8 L32 32" stroke="var(--red)" stroke-width="2.5"/>
    </svg>
  </section>

  <p class="bill-summary">Lorem ipsum dolor sit amet, consectetur adipiscing elit. Nam condimentum leo sed nisi malesuada, sed accumsan metus ultricies. Donec eleifend nibh in ultrices tempus. Morbi id tempor lorem. Suspendisse potenti. Fusce at augue pulvinar, ultricies nisl id, bibendum est. Cras semper ac nulla ut vulputate. Nam faucibus sagittis odio, quis molestie elit sollicitudin et. Nam dapibus fringilla orci, quis efficitur leo consectetur eu. Vivamus dui lectus, mollis a condimentum consequat, ullamcorper porta lectus. Vivamus sit amet justo enim. Donec nec lorem mi. Lorem ipsum dolor sit amet, consectetur adipiscing elit. Nam condimentum leo sed nisi malesuada, sed accumsan metus ultricies. Donec eleifend nibh in ultrices tempus. Morbi id tempor lorem. Suspendisse potenti. Fusce at augue pulvinar, ultricies nisl id, bibendum est. Cras semper ac nulla ut vulputate. Nam faucibus sagittis odio, quis molestie elit sollicitudin et. Nam dapibus fringilla orci, quis efficitur leo consectetur eu. Vivamus dui lectus, mollis a condimentum consequat, ullamcorper porta lectus. Vivamus sit amet justo enim. Donec nec lorem mi. Lorem ipsum dolor sit amet, consectetur adipiscing elit. Nam condimentum leo sed nisi malesuada, sed accumsan metus ultricies. Donec eleifend nibh in ultrices tempus. Morbi id tempor lorem. Suspendisse potenti. Fusce at augue pulvinar, ultricies nisl id, bibendum est. Cras semper ac nulla ut vulputate. Nam faucibus sagittis odio, quis molestie elit sollicitudin et. Nam dapibus fringilla orci, quis efficitur leo consectetur eu. Vivamus dui lectus, mollis a condimentum consequat, ullamcorper porta lectus.</p>

  <div class="vote-actions">
    <div class="vote no">
      <div class="vote-circle">
        <svg width="26" height="26" viewBox="0 0 26 26" aria-hidden="true">
          <path d="M4 4 L22 22 M22 4 L4 22" stroke="#fff" stroke-width="3.5" stroke-linecap="round"/>
        </svg>
      </div>
      <span class="vote-label">No</span>
    </div>
    <div class="vote party">
      <div class="vote-circle">
        <svg width="34" height="34" viewBox="0 0 34 34" aria-hidden="true">
          <path d="M5 7 H27 L16 19 Z" fill="#fff"/>
          <path d="M16 19 V29 M10 29 H22" stroke="#fff" stroke-width="2.2" stroke-linecap="round"/>
          <circle cx="25" cy="6" r="3.5" fill="none" stroke="#fff" stroke-width="1.6"/>
        </svg>
      </div>
      <span class="vote-label">Party</span>
    </div>
    <div class="vote yes">
      <div class="vote-circle">
        <svg width="32" height="28" viewBox="0 0 32 28" aria-hidden="true">
          <path d="M4 15 L12 23 L28 5" fill="none" stroke="#fff" stroke-width="3.8" stroke-linecap="round" stroke-linejoin="round"/>
        </svg>
      </div>
      <span class="vote-label">Yes</span>
    </div>
  </div>

  <footer class="chamber-bar">
    <span class="live-dot"></span>
    <span class="chamber">Legislative Council</span>
    <span class="count">1 / 77</span>
  </footer>
</body>
</html>
```